Harrowgate Care Assurance Ltd needs a business card and logo

We need a logo for documents, invoices etc and a business card to match. We are a health auditing, training and consulting company based in NZ and working in both Australia and NZ. We ensure health organisations meet all their compliance requirements and develop expertise in the health auditing sector. The design should in some way reflect either symbols for quality management in the health sector.

Target Market(s)

Health providers and those wishing to increase their capability in meeting and understanding compliance requirements

Industry/Entity Type

Business

Contact Information for Business Card

Logo plus contact details

Logo Text

Health auditing, consultancy and training

Requirements
Must have
• Name and contact details director: Marla Fenwick, mfenwick@hca-example.co.nz, PO Box 318, Warkworth, NZ, cell +6427391652

```html
<!DOCTYPE html>
<html lang="en">
<head>
<meta charset="utf-8">
<title>Harrowgate Care Assurance Ltd — Business Card</title>
<link rel="stylesheet" href="https://fonts.googleapis.com/css2?family=Open+Sans:wght@400;600;700&display=swap">
<style>
  :root {
    --backdrop: #262626;
    --brand-blue: #0f6fb8;
    --brand-blue-deep: #075a9c;
    --brand-blue-light: #1a88d0;
    --ink: #2b2b2b;
    --stripe-dark: #2d2d2d;
    --paper: #ffffff;
  }
  * { margin: 0; padding: 0; box-sizing: border-box; }
  html, body {
    width: 1200px; height: 1001px; overflow: hidden;
    background: var(--backdrop);
    font-family: "Open Sans", Arial, sans-serif;
  }
  .canvas { position: relative; width: 1200px; height: 1001px; }
  .card {
    position: absolute; left: 276px; width: 618px; height: 380px;
    border-radius: 12px; overflow: hidden;
  }
  .card--front {
    top: 99px;
    background: radial-gradient(ellipse 260px 210px at 50% 38%, var(--brand-blue-light), var(--brand-blue-deep) 100%);
  }
  .card--back { top: 511px; background: var(--paper); }

  .brand { position: absolute; display: flex; align-items: center; }
  .brand__dot { border-radius: 50%; flex: none; }
  .brand__name { text-transform: uppercase; font-weight: 400; line-height: 1.15; }
  .brand__name span { display: block; }
  .brand__name .brand__line-1 { font-size: 21px; letter-spacing: 1px; }
  .brand__name .brand__line-2 { font-size: 13px; letter-spacing: 4px; }

  .card--front .brand { left: 139px; top: 138px; }
  .card--front .brand__dot { width: 110px; height: 110px; background: var(--paper); margin-right: 12px; }
  .card--front .brand__name { color: var(--paper); }

  .card--back .brand { left: 241px; top: 50px; }
  .card--back .brand__dot { width: 104px; height: 104px; background: var(--brand-blue); margin-right: 10px; }
  .card--back .brand__name { color: var(--ink); }
  .card--back .brand__name .brand__line-1 { font-size: 19px; }
  .card--back .brand__name .brand__line-2 { font-size: 12px; letter-spacing: 3.5px; }

  .holder {
    position: absolute; left: 40px; right: 35px; top: 251px;
    display: flex; align-items: center;
  }
  .holder__name {
    color: var(--brand-blue); font-weight: 700; font-size: 16px; letter-spacing: 1px;
    text-transform: uppercase; margin-right: 6px; white-space: nowrap;
  }
  .holder__rule { flex: 1; height: 2px; background: var(--brand-blue); }

  .contact { position: absolute; left: 38px; top: 292px; font-size: 15.5px; color: var(--ink); }
  .contact__row { display: flex; align-items: center; height: 21px; }
  .contact__icon { width: 16px; height: 14px; margin-right: 5px; }
  .address { position: absolute; right: 38px; top: 312px; font-size: 15.5px; color: var(--ink); }

  .footer-band { position: absolute; left: 0; bottom: 0; width: 618px; height: 34px; }
</style>
</head>
<body>
<main class="canvas">
  <section class="card card--front" aria-label="Card front">
    <div class="brand">
      <div class="brand__dot"></div>
      <p class="brand__name"><span class="brand__line-1">Harrowgate Care</span><span class="brand__line-2">Assurance Ltd</span></p>
    </div>
  </section>

  <section class="card card--back" aria-label="Card back">
    <div class="brand">
      <div class="brand__dot"></div>
      <p class="brand__name"><span class="brand__line-1">Harrowgate Care</span><span class="brand__line-2">Assurance Ltd</span></p>
    </div>

    <div class="holder">
      <span class="holder__name">Marla Fenwick</span>
      <span class="holder__rule"></span>
    </div>

    <div class="contact">
      <div class="contact__row">
        <svg class="contact__icon" viewBox="0 0 16 14" aria-hidden="true">
          <rect x="4" y="0.5" width="8" height="13" rx="1.2" fill="none" stroke="var(--brand-blue)" stroke-width="1.6"/>
          <rect x="6.5" y="11" width="3" height="1" fill="var(--brand-blue)"/>
        </svg>
        <span>+6427391652</span>
      </div>
      <div class="contact__row">
        <svg class="contact__icon" viewBox="0 0 16 14" aria-hidden="true">
          <rect x="0.5" y="2.5" width="15" height="10" fill="var(--brand-blue)"/>
          <path d="M0.5 2.5 L8 8.5 L15.5 2.5" fill="none" stroke="#fff" stroke-width="1.2"/>
        </svg>
        <span>mfenwick@hca-example.co.nz</span>
      </div>
    </div>

    <p class="address">PO Box 318, Warkworth, NZ</p>

    <svg class="footer-band" viewBox="0 0 618 34" aria-hidden="true">
      <path d="M0 23 L618 23 L618 34 L0 34 Z" fill="var(--brand-blue)"/>
      <path d="M0 5 L352 5 C336 7 332 14 326 17 L0 17 Z" fill="var(--stripe-dark)"/>
      <path d="M352 1 L618 1 L618 34 L322 34 L322 20 C338 14 338 2 352 1 Z" fill="var(--brand-blue)"/>
    </svg>
  </section>
</main>
</body>
</html>
```